New Innovative Counselling and psychotherapy Service needs Business Card design

Keep it simple and professional. On one side, just company name and logo (perhaps in all blue) and maybe a tag line.

On other side (all white) my name and Qualifications in centre

Industry/Entity Type

Health And Wellness

Contact Information for Business Card

Dara Whelby
Counsellor & Psychotherapist
MSc (Couns.), BA, Dip. (Fam. Ther.), PG.Dip (DBT), FGTrK, ONRE

I will also require Mobile no, Email and web site address of which I'll pass on to final designer.

Font styles to use
Sans Serif

Requirements
Must have
• My Logo Only and please use the colours in logo that is in it.
Should not have
• Any other images

```html
<!DOCTYPE html>
<html lang="en">
<head>
<meta charset="utf-8">
<title>Calmer Lane – Business Card</title>
<link href="https://fonts.googleapis.com/css2?family=Open+Sans:wght@400;600;700&display=swap" rel="stylesheet">
<style>
  :root {
    --canvas-bg: #e9ecef;
    --sky-light: #66daf8;
    --sky-deep: #3aa8ea;
    --brand-blue: #3aa2e8;
    --brand-green: #8cc63f;
    --ink: #3b3f45;
    --ink-soft: #4a5866;
    --rule: #6c7177;
    --paper: #ffffff;
  }
  * { box-sizing: border-box; margin: 0; padding: 0; }
  html, body { width: 1200px; height: 900px; overflow: hidden; }
  body {
    background: var(--canvas-bg);
    font-family: "Open Sans", Arial, sans-serif;
    position: relative;
  }
  .card {
    position: absolute;
    left: 250px;
    width: 700px;
    height: 400px;
    box-shadow: 0 6px 18px rgba(0,0,0,.12);
  }
  .card--front {
    top: 40px;
    background: linear-gradient(100deg, var(--sky-light) 0%, var(--sky-deep) 100%);
  }
  .card--back { top: 465px; background: var(--paper); }

  .brand {
    position: absolute;
    display: flex;
    align-items: center;
    gap: 18px;
  }
  .brand__dot {
    width: 62px; height: 62px; border-radius: 50%;
    background: var(--paper);
  }
  .brand__name {
    font-size: 40px; font-weight: 400; color: var(--ink);
    letter-spacing: -0.5px;
  }
  .card--front .brand { left: 180px; top: 150px; }
  .tagline {
    position: absolute; left: 0; right: 0; bottom: 40px;
    text-align: center; font-size: 17px; color: var(--ink-soft);
  }

  .card--back .brand { left: 430px; top: 170px; gap: 14px; }
  .card--back .brand__dot { width: 44px; height: 44px; background: var(--brand-blue); }
  .card--back .brand__name { font-size: 30px; }

  .timeline {
    position: absolute; left: 58px; top: 0; bottom: 0;
    width: 2px; background: var(--rule);
  }
  .icon {
    position: absolute; left: 42px;
    width: 34px; height: 34px; border-radius: 50%;
    display: flex; align-items: center; justify-content: center;
  }
  .icon--blue { background: var(--brand-blue); }
  .icon--green { background: var(--brand-green); }
  .icon svg { width: 18px; height: 18px; }

  .person { position: absolute; left: 100px; top: 48px; }
  .person__name {
    font-size: 26px; font-weight: 700; color: var(--brand-blue);
    text-transform: uppercase; line-height: 1.1;
  }
  .person__role {
    font-size: 21px; font-weight: 400; color: var(--brand-green);
    text-transform: uppercase; line-height: 1.25;
  }
  .person__quals {
    font-size: 14px; color: var(--brand-green); line-height: 1.35; margin-top: 3px;
  }
  .contact {
    position: absolute; left: 100px;
    font-size: 18px; line-height: 25px; color: var(--ink);
  }
</style>
</head>
<body>
  <section class="card card--front">
    <div class="brand">
      <span class="brand__dot"></span>
      <span class="brand__name">Calmer Lane</span>
    </div>
    <p class="tagline">Steady Support For A Clearer And Calmer Mind Every Day</p>
  </section>

  <section class="card card--back">
    <span class="timeline"></span>

    <span class="icon icon--blue" style="top:58px">
      <svg viewBox="0 0 20 20" fill="#fff"><circle cx="10" cy="6.5" r="4"/><path d="M2.5 18c0-4.2 3.4-7 7.5-7s7.5 2.8 7.5 7z"/></svg>
    </span>
    <span class="icon icon--green" style="top:196px">
      <svg viewBox="0 0 20 20" fill="none" stroke="#fff" stroke-width="2"><rect x="5.5" y="2" width="9" height="16" rx="1.5"/><circle cx="10" cy="15" r=".6" fill="#fff"/></svg>
    </span>
    <span class="icon icon--blue" style="top:256px">
      <svg viewBox="0 0 20 20" fill="none" stroke="#fff" stroke-width="1.8"><rect x="2.5" y="5" width="15" height="10" rx="1"/><path d="M2.5 5.5 10 11l7.5-5.5"/></svg>
    </span>
    <span class="icon icon--green" style="top:316px">
      <svg viewBox="0 0 20 20" fill="none" stroke="#fff" stroke-width="1.6"><circle cx="10" cy="10" r="7.5"/><ellipse cx="10" cy="10" rx="3.2" ry="7.5"/><path d="M2.5 10h15"/></svg>
    </span>

    <div class="person">
      <h1 class="person__name">Dara Whelby</h1>
      <p class="person__role">Counsellor &amp; Psychotherapist</p>
      <p class="person__quals">MSc (Couns.), BA, Dip. (Fam. Ther.),<br>PG.Dip (DBT), FGTrK, ONRE</p>
    </div>

    <p class="contact" style="top:200px">555 210 4478</p>
    <p class="contact" style="top:260px">dara@Calmerlane.com</p>
    <p class="contact" style="top:320px">www.Calmerlane.com</p>

    <div class="brand">
      <span class="brand__dot"></span>
      <span class="brand__name">Calmer Lane</span>
    </div>
  </section>
</body>
</html>
```